all natural handmade soap company looking for unique stand out packaging design for bar soaps

we are looking for a unique and stand out on the shelf package design for our hand made soaps for grocery stores. we have a package soap box (picture included) but we are looking for a TOP-NOTCH, CUSTOM, STAND OUT DESIGN FOR THEM. I am supplying our current packaging design, but we want something more unique and STAND OUT. PICTURES i AM INCLUDING ARE: 1: OUR CURRENT PACKAGE DESIGN
2: OUR LIQUID SOAP LABELS (WHICH WE LOVE) AND WOULD LIKE THE BAR SOAPS TO BE SIMILAR
3: WILL BE IN A WHITE BOX WITH A LARGE CUT OUT IN FRONT (SEE SAMPLE BOX BROWN KRAFT).

Target Market(s)

VARIOUS CUSTOMERS. We sell to bright lantern grocers and various grocery stores

Industry/Entity Type

It Company

Requirements
Must have
• cool, unique look that will stand out from a store shelf
• full color acceptable
• our logo on the round part of the package (front)
• please leave a space for bar codes (usually on bottom of box)
• there is a cut out (front) that is there for people to see, feel and smell the soap
• be creative think outside the box open to fresh new designs
Nice to have
• metallic crescent moon (our logo)
Should not have
• organic cannot appear on the front

```html
<!DOCTYPE html>
<html lang="en">
<head>
<meta charset="utf-8">
<title>Lumivale Lemon Natural Soap – Packaging</title>
<link rel="stylesheet" href="https://fonts.googleapis.com/css2?family=Cormorant+Garamond:wght@400&family=Playfair+Display:wght@700;900&family=Open+Sans:wght@400&display=swap">
<style>
  :root {
    --lemon: #f2e10e;
    --pale-lemon: #fbf3a6;
    --white: #ffffff;
    --ink: #0d0d0d;
    --frame: #c8c8c8;
    --seal-edge: #d6d6d6;
    --fruit-light: #f6dc4a;
    --fruit-mid: #efc72a;
    --fruit-deep: #e2b21e;
  }
  * { margin: 0; padding: 0; box-sizing: border-box; }
  html, body { width: 1200px; height: 824px; overflow: hidden; background: var(--white); }
  .sheet { position: relative; width: 1200px; height: 824px; }

  .package {
    position: absolute; top: 55px; width: 497px; height: 706px;
    border: 1.5px solid var(--frame); background: var(--white); overflow: hidden;
  }
  .package--yellow-seal { left: 63px; }
  .package--white-seal { left: 628px; }

  .top-field { position: absolute; left: 0; top: 0; width: 100%; height: 187px; border-bottom: 1px solid var(--frame); }
  .top-field--pattern { background: var(--pale-lemon); opacity: .75; }
  .top-field--solid { background: var(--lemon); }

  .seal { position: absolute; left: 248px; top: 201px; border-radius: 50%; transform: translate(-50%, -50%); }
  .seal--outer { width: 364px; height: 364px; }
  .package--yellow-seal .seal--outer { background: var(--lemon); }
  .package--white-seal .seal--outer { background: var(--white); border: 2px solid var(--seal-edge); }
  .seal--ring { width: 342px; height: 342px; }
  .package--yellow-seal .seal--ring { border: 3px solid var(--white); }
  .package--white-seal .seal--ring { border: 2.5px solid var(--lemon); }

  .seal-content { position: absolute; left: 66px; top: 19px; width: 364px; height: 364px; }
  .seal-text { position: absolute; left: 0; width: 100%; text-align: center; color: var(--ink); }
  .brand-name { top: 89px; font-family: "Cormorant Garamond", serif; font-size: 30px; letter-spacing: 1.5px; line-height: 1; }
  .tagline { top: 172px; font-family: "Playfair Display", serif; font-weight: 700; font-size: 22px; line-height: 1; }
  .product-type { top: 202px; font-family: "Playfair Display", serif; font-weight: 700; font-size: 50px; line-height: 49px; }

  .scent-band { position: absolute; left: 0; top: 529px; width: 100%; height: 90px; background: var(--lemon); }
  .bottom-field { position: absolute; left: 0; top: 619px; width: 100%; height: 87px; background: var(--pale-lemon); opacity: .75; }
  .scent-name {
    position: absolute; right: 36px; top: 538px;
    font-family: "Playfair Display", serif; font-weight: 900; font-size: 60px; line-height: 70px;
    color: var(--ink); letter-spacing: 1px;
  }
  .net-weight {
    position: absolute; right: 40px; top: 636px;
    font-family: "Open Sans", sans-serif; font-size: 18px; color: var(--ink);
  }
  .fruit-photo {
    position: absolute; left: 20px; top: 508px; width: 217px; height: 160px;
    border-radius: 10px;
    background: linear-gradient(135deg, var(--fruit-light), var(--fruit-mid) 55%, var(--fruit-deep));
  }
</style>
</head>
<body>
<main class="sheet">

  <section class="package package--yellow-seal">
    <div class="top-field top-field--pattern" role="img" aria-label="Pale yellow hand-brushed dash pattern"></div>
    <div class="seal seal--outer"></div>
    <div class="seal seal--ring"></div>
    <div class="seal-content">
      <p class="seal-text brand-name">LUMIVALE</p>
      <p class="seal-text tagline">Handcrafted Artisan</p>
      <h1 class="seal-text product-type">NATURAL<br>SOAP</h1>
    </div>
    <div class="scent-band"></div>
    <div class="bottom-field" role="img" aria-label="Pale yellow hand-brushed dash pattern"></div>
    <h2 class="scent-name">LEMON</h2>
    <p class="net-weight">4.5 oz (127.57 grams)</p>
    <div class="fruit-photo" role="img" aria-label="Photo of whole lemons with leaves and a halved lemon"></div>
  </section>

  <section class="package package--white-seal">
    <div class="top-field top-field--solid"></div>
    <div class="seal seal--outer"></div>
    <div class="seal seal--ring"></div>
    <div class="seal-content">
      <p class="seal-text brand-name">LUMIVALE</p>
      <p class="seal-text tagline">Handcrafted Artisan</p>
      <h1 class="seal-text product-type">NATURAL<br>SOAP</h1>
    </div>
    <div class="scent-band"></div>
    <div class="bottom-field" role="img" aria-label="Pale yellow hand-brushed dash pattern"></div>
    <h2 class="scent-name">LEMON</h2>
    <p class="net-weight">4.5 oz (127.57 grams)</p>
    <div class="fruit-photo" role="img" aria-label="Photo of whole lemons with leaves and a halved lemon"></div>
  </section>

</main>
</body>
</html>
```